Small environmental consultancy needs a simple but professional web design

We are a boutique environmental consultancyand contracting business located in Margaret River in the South West of Western Australia.

We have two arms
1) Consulting which offers environmental planning, management and assessment services primarily to local government and the development industry.
2) Contracting which implements on site plans and on ground works primarily involving revegetation, bush regeneration and environmental weed control.

We need a simple yet professional web design within the wordpress platform that commmunicates professionalism, experience and technical expertise without appearing too corporate.

Something like this structure appeals:
http://fernquill.net.au/environment-services/
or
http://www.tallowbrookenvironmental.com.au/index.php

(without the image gallery function)

Target Market(s)

Local Government Officers deciding on tenders;
Developers, Engineers, Town Planning consultants looking for environmental expertise

Industry/Entity Type

Business

Number of Pages Required

5+ page

Font styles to use
Sans Serif

Colors
33a6d7
9bcb3c

Requirements
Must have
• Pages required include:
• Home
• Environmental Planning and Management
• Revegetation and Regeneration Implementation (This page can mirror the Environmental Planning and Management page exactly in structure but with different text and images)
• About Us (I think that this page can be relatively simple and generic)
• Contact (I think that this page can be very simple and generic)
Nice to have
• An ability to start out basic and quicikly establish a website presence and then build in additional drop downs and pages over time.
Should not have
• It does not need a photo gallery page;
• It does not need a major amount of space dedicated to social media and blogs etc as this is not currently particularly active area for us

```html
<!DOCTYPE html>
<html lang="en">
<head>
<meta charset="utf-8">
<title>Karri Ridge Ecoservices — Environmental Consultants</title>
<link href="https://fonts.googleapis.com/css2?family=Montserrat:wght@400;600;700&family=Open+Sans:wght@400;600&display=swap" rel="stylesheet">
<style>
:root{
  --blue:#33a6d7;
  --green:#9bcb3c;
  --nav-green:#8cc63f;
  --ink:#1a1a1a;
  --body:#5a5a5a;
  --rule:#e4e4e4;
  --card:#f3f3f3;
  --footer:#000;
  --brand:#6b8e23;
}
*{margin:0;padding:0;box-sizing:border-box}
html,body{width:945px;height:1200px;overflow:hidden;background:#fff}
body{position:relative;font-family:"Open Sans",Arial,sans-serif;color:var(--body)}

/* header */
.site-header{position:absolute;left:0;top:0;width:945px;height:107px;background:#fff;box-shadow:0 1px 3px rgba(0,0,0,.15);z-index:2}
.brand{position:absolute;left:58px;top:14px;width:140px;text-align:center}
.brand-mark{display:block;width:40px;height:40px;border-radius:50%;background:var(--nav-green);margin:0 auto 6px}
.brand-name{font-family:"Montserrat",sans-serif;font-weight:600;font-size:12.5px;color:var(--brand);white-space:nowrap}
.call{position:absolute;right:260px;top:30px;font-family:"Montserrat",sans-serif;font-size:11px;color:var(--ink);white-space:nowrap}
.call strong{font-size:13.5px;color:var(--blue);font-weight:600;margin-left:3px}
.search{position:absolute;left:697px;top:27px;width:190px;height:22px;border:1px solid #cfcfcf;border-radius:2px;font-size:10.5px;color:#aaa;padding:3px 8px}
.search svg{position:absolute;right:6px;top:4px}
.main-nav{position:absolute;top:77px;left:237px;width:649px;display:flex;justify-content:space-between;font-family:"Montserrat",sans-serif;font-weight:600;font-size:9.1px;color:var(--ink);text-transform:uppercase;letter-spacing:-.1px}
.main-nav a{color:inherit;text-decoration:none;position:relative;white-space:nowrap}
.main-nav a.current::after{content:"";position:absolute;left:0;right:0;top:16px;height:2px;background:var(--nav-green)}

/* hero */
.hero{position:absolute;left:0;top:107px;width:945px;height:388px;background:linear-gradient(180deg,#c9ccd0 0%,#a9adb4 22%,#7b8a70 40%,#4f6e2e 62%,#2e4a18 100%)}
.hero-arrow{position:absolute;width:26px;height:26px;border-radius:50%;background:rgba(255,255,255,.9);top:181px}
.hero-arrow svg{position:absolute;left:8px;top:7px}
.hero-title{position:absolute;left:556px;top:258px;font-family:"Montserrat",sans-serif;font-weight:700;font-size:26px;color:#fff;letter-spacing:-.5px;line-height:1;white-space:nowrap}
.hero-sub{position:absolute;left:557px;top:288px;font-family:"Montserrat",sans-serif;font-size:12.5px;color:#fff;text-transform:uppercase;letter-spacing:-.2px;white-space:nowrap}

/* intro */
.intro{position:absolute;left:57px;top:520px;width:548px}
.intro h1{font-family:"Montserrat",sans-serif;font-size:16.5px;line-height:19px;color:var(--ink);font-weight:700;text-transform:uppercase}
.intro h1 span{display:block;font-weight:400}
.intro p{font-size:10.9px;line-height:16.8px;margin-top:17px}
.intro h1 + p{margin-top:21px}

/* services */
.services{position:absolute;left:626px;top:469px;width:261px;height:302px;background:#fff;box-shadow:0 2px 8px rgba(0,0,0,.12)}
.services-head{background:var(--blue);height:65px;padding:18px 20px 0;font-family:"Montserrat",sans-serif;font-size:16.5px;line-height:18px;color:#fff;text-transform:uppercase}
.services-head b{display:block;font-weight:700}
.services ul{list-style:none;padding:17px 8px 0 20px}
.services li{position:relative;padding-left:18px;font-size:10.1px;line-height:13px;margin-bottom:13px;color:var(--body)}
.services li svg{position:absolute;left:0;top:1px}

.divider{position:absolute;left:57px;top:788px;width:830px;height:1px;background:var(--rule)}

/* projects */
.section-title{position:absolute;left:57px;top:819px;font-family:"Montserrat",sans-serif;font-size:17px;font-weight:400;color:var(--ink);text-transform:uppercase}
.section-title b{font-weight:700}
.btn-more{position:absolute;left:767px;top:818px;width:110px;height:23px;background:var(--green);border-radius:2px;color:#fff;font-family:"Montserrat",sans-serif;font-size:9px;line-height:23px;text-align:center;text-transform:uppercase;white-space:nowrap}
.projects{position:absolute;left:58px;top:863px;width:829px;height:269px;border:1px solid var(--rule);padding:6px}
.project-grid{display:flex}
.project{width:203.5px;height:253px;background:var(--card);position:relative;border-right:1px solid #e6e6e6}
.project:last-child{border-right:0}
.project-photo{height:150px;position:relative}
.project h3{font-size:11.6px;font-weight:600;color:var(--ink);padding:8px 10px 0;line-height:16px}
.project p{font-size:10.8px;line-height:16px;padding:7px 10px 0}
.zoom{position:absolute;left:76px;top:49px;width:52px;height:52px;border-radius:50%;background:rgba(255,255,255,.7)}
.zoom svg{position:absolute;left:19px;top:19px}

/* footer */
.site-footer{position:absolute;left:0;top:1161px;width:945px;height:39px;background:var(--footer);color:#ddd;font-size:10px;padding:15px 58px 0;display:flex;justify-content:space-between}
.site-footer b{color:#fff;font-weight:600}
.site-footer .copy{color:#999}
</style>
</head>
<body>

<header class="site-header">
  <div class="brand">
    <span class="brand-mark"></span>
    <span class="brand-name">Karri Ridge Ecoservices</span>
  </div>
  <div class="call">Call Us now On <strong>1.888.440.2716</strong></div>
  <div class="search">Search
    <svg width="13" height="13" viewBox="0 0 13 13"><circle cx="5.5" cy="5.5" r="4.2" fill="none" stroke="#999" stroke-width="1.5"/><line x1="8.6" y1="8.6" x2="12" y2="12" stroke="#999" stroke-width="1.6"/></svg>
  </div>
  <nav class="main-nav">
    <a class="current" href="#">Home</a>
    <a href="#">Environmental Planning &amp; Management</a>
    <a href="#">Revegetation &amp; Regeneration Implementation</a>
    <a href="#">About</a>
    <a href="#">Contact</a>
  </nav>
</header>

<section class="hero" role="img" aria-label="Alpine meadow of yellow wildflowers with snowy mountains under a cloudy sky">
  <div class="hero-arrow" style="left:57px"><svg width="10" height="12" viewBox="0 0 10 12"><path d="M7 1 2 6l5 5" fill="none" stroke="#333" stroke-width="1.8"/></svg></div>
  <div class="hero-arrow" style="left:860px"><svg width="10" height="12" viewBox="0 0 10 12"><path d="M3 1l5 5-5 5" fill="none" stroke="#333" stroke-width="1.8"/></svg></div>
  <div class="hero-title">LOREM IPSUM DOLOR</div>
  <div class="hero-sub">Dosis amet sit lorem ipsum delite</div>
</section>

<section class="intro">
  <h1>Karri Ridge Ecoservices<span>Environmental Consultants</span></h1>
  <p>Lorem ipsum dolor sit amet, consectetuer adipiscing elit, sed diam nonummy nibh euismod tincidunt ut laoreet dolore magna aliquam erat ullamcorper suscipit lobortis nisl ut aliquip ex ea commodo consequat. Lorem ipsum dolor sit amet, consectetuer adipiscing elit, sed diam nonummy nibh euismod incidunt ut laoreet dolore magna aliquam erat volutpat. Ut wisi enim ad minim veniam, quis nostrud exerci tation ullamcorper suscipit lobortis nisl ut aliquip ex ea commodo consequat.</p>
  <p>Lorem ipsum dolor sit amet, consectetuer adipiscing elit, sed diam nonummy nibh euismod incidunt ut laoreet dolore magna aliquam erat volutpat. Ut wisi enim ad minim veniam, quis nostrud exerci tation ullamcorper suscipit lobortis nisl ut aliquip ex ea commodo consequat.t wisi enim ad minim veniam, quis nostrud exerci tation ullamcorper suscipit lobortis nisl ut aliquip ex ea commodo consequat.</p>
</section>

<aside class="services">
  <div class="services-head"><b>Environmental</b>Services</div>
  <ul>
    <li><svg width="11" height="11" viewBox="0 0 11 11"><g stroke="#aaa" stroke-width="1.3"><line x1="5.5" y1="0" x2="5.5" y2="11"/><line x1="0" y1="5.5" x2="11" y2="5.5"/><line x1="1.6" y1="1.6" x2="9.4" y2="9.4"/><line x1="9.4" y1="1.6" x2="1.6" y2="9.4"/></g></svg>Lorem ipsum dolor sit amet, consectetuer adipiscing elit</li>
    <li><svg width="11" height="11" viewBox="0 0 11 11"><g stroke="#aaa" stroke-width="1.3"><line x1="5.5" y1="0" x2="5.5" y2="11"/><line x1="0" y1="5.5" x2="11" y2="5.5"/><line x1="1.6" y1="1.6" x2="9.4" y2="9.4"/><line x1="9.4" y1="1.6" x2="1.6" y2="9.4"/></g></svg>Lorem ipsum dolor ctetuer adipiscing elit</li>
    <li><svg width="11" height="11" viewBox="0 0 11 11"><g stroke="#aaa" stroke-width="1.3"><line x1="5.5" y1="0" x2="5.5" y2="11"/><line x1="0" y1="5.5" x2="11" y2="5.5"/><line x1="1.6" y1="1.6" x2="9.4" y2="9.4"/><line x1="9.4" y1="1.6" x2="1.6" y2="9.4"/></g></svg>Lorem ipsum dolor sit amet, consectetuer adipiscing elit</li>
    <li><svg width="11" height="11" viewBox="0 0 11 11"><g stroke="#aaa" stroke-width="1.3"><line x1="5.5" y1="0" x2="5.5" y2="11"/><line x1="0" y1="5.5" x2="11" y2="5.5"/><line x1="1.6" y1="1.6" x2="9.4" y2="9.4"/><line x1="9.4" y1="1.6" x2="1.6" y2="9.4"/></g></svg>Lorem ipsum dolor ctetuer adipiscing elit</li>
    <li><svg width="11" height="11" viewBox="0 0 11 11"><g stroke="#aaa" stroke-width="1.3"><line x1="5.5" y1="0" x2="5.5" y2="11"/><line x1="0" y1="5.5" x2="11" y2="5.5"/><line x1="1.6" y1="1.6" x2="9.4" y2="9.4"/><line x1="9.4" y1="1.6" x2="1.6" y2="9.4"/></g></svg>Lorem ipsum dolor sit amet, consectetuer adipiscing elit</li>
    <li><svg width="11" height="11" viewBox="0 0 11 11"><g stroke="#aaa" stroke-width="1.3"><line x1="5.5" y1="0" x2="5.5" y2="11"/><line x1="0" y1="5.5" x2="11" y2="5.5"/><line x1="1.6" y1="1.6" x2="9.4" y2="9.4"/><line x1="9.4" y1="1.6" x2="1.6" y2="9.4"/></g></svg>Lorem ipsum dolor ctetuer adipiscing elit</li>
    <li><svg width="11" height="11" viewBox="0 0 11 11"><g stroke="#aaa" stroke-width="1.3"><line x1="5.5" y1="0" x2="5.5" y2="11"/><line x1="0" y1="5.5" x2="11" y2="5.5"/><line x1="1.6" y1="1.6" x2="9.4" y2="9.4"/><line x1="9.4" y1="1.6" x2="1.6" y2="9.4"/></g></svg>Dolor sit amet, consectetuer adipiscing elit</li>
  </ul>
</aside>

<div class="divider"></div>

<h2 class="section-title"><b>Recent</b> Project</h2>
<a class="btn-more">View More Project</a>

<section class="projects">
  <div class="project-grid">
    <article class="project">
      <div class="project-photo" role="img" aria-label="Cluster of red ixora flowers among green leaves" style="background:linear-gradient(160deg,#2f4a1f 0%,#c9402a 45%,#e05a35 70%,#3a3a1c 100%)"></div>
      <h3>Lorem Ipsum Generator</h3>
      <p>In publishing and graphic design, lorem ipsum is a filler text used to demonstrate the graphic elements presentation[...]</p>
    </article>
    <article class="project">
      <div class="project-photo" role="img" aria-label="Close-up of a red and orange tropical flower" style="background:radial-gradient(circle at 50% 50%,#e2593a 0%,#b7352a 35%,#3e3a14 75%,#24290e 100%)">
        <div class="zoom"><svg width="14" height="14" viewBox="0 0 14 14"><circle cx="6" cy="6" r="4.3" fill="none" stroke="#222" stroke-width="1.8"/><line x1="9.2" y1="9.2" x2="13" y2="13" stroke="#222" stroke-width="2"/></svg></div>
      </div>
      <h3>Lorem Ipsum Generator</h3>
      <p>In publishing and graphic design, lorem ipsum is a filler text used to demonstrate the graphic elements presentation[...]</p>
    </article>
    <article class="project">
      <div class="project-photo" role="img" aria-label="Red ixora blossoms against a blue sky" style="background:linear-gradient(200deg,#5f8fd0 0%,#7aa3d8 35%,#c0432e 65%,#3e5a24 100%)"></div>
      <h3>Lorem Ipsum Generator</h3>
      <p>In publishing and graphic design, lorem ipsum is a filler text used to demonstrate the graphic elements presentation[...]</p>
    </article>
    <article class="project">
      <div class="project-photo" role="img" aria-label="Purple thistle flower head on a pale green background" style="background:radial-gradient(circle at 50% 35%,#d23ac0 0%,#b43ea8 25%,#9fbf6a 55%,#6e9a3c 100%)"></div>
      <h3>Lorem Ipsum Generator</h3>
      <p>In publishing and graphic design, lorem ipsum is a filler text used to demonstrate the graphic elements presentation[...]</p>
    </article>
  </div>
</section>

<footer class="site-footer">
  <span><b>Contact Info :</b> 200 Lorem Ipsum dolor sir- VA 348595 &nbsp;|&nbsp; Tel: (800) 314 77 6021 &nbsp;|&nbsp; Fax: (800) 314 77 6021</span>
  <span class="copy">© 2015 Karri Ridge Ecoservices.</span>
</footer>

</body>
</html>
```